FinTech company looking to revamp and expand client-facing interface for our financial models

Pellworth Engines currently has a very simple website that allows clients to interact with our financial models. We are looking to completely redesign the current site and add several extra pages to provide extra functionality. We want the design to have a modern, slick feel, that will work on both a desktop or a tablet. It should be straightforward for clients to move between different pages at any time, and clear from the layout how to interact with the more advanced features. We have included screenshots of existing pages in the attached design brief, as well as sketches of the functionality required by the new pages, but can't provide a direct link to the current site.
Target Market(s)
Professional investors that will be paying to access the interface
Industry/Entity Type
Finance
Number of Pages Required
4 page
Colors
Designer to choose colors to be used in the design.
Look and feel
Each slider illustrates characteristics of the customer's brand and the style your logo design should communicate.

```html
<!DOCTYPE html>
<html lang="en">
<head>
<meta charset="utf-8">
<title>Pellworth Engines · ETF Pairs</title>
<link href="https://fonts.googleapis.com/css2?family=Montserrat:wght@500;600;700&family=Roboto+Condensed:wght@400&display=swap" rel="stylesheet">
<style>
:root{
  --navy:#053a73;
  --teal:#006b63;
  --ink:#1b1b1b;
  --grey-badge:#9a9a9a;
  --page:#e6e6e6;
  --row-alt:#f1f1f1;
  --line:#e2e2e2;
  --blue:#3a6fb0;
  --olive:#bdb738;
  --green:#4a9a3c;
}
*{box-sizing:border-box;margin:0;padding:0}
html,body{width:1040px;height:1200px;overflow:hidden;background:var(--page);font-family:'Montserrat',sans-serif;color:var(--ink)}
.frame{position:absolute;left:12px;top:12px;width:1016px;height:1176px;background:linear-gradient(#ececec 0,#e9e9e9 140px,#f7f7f7 400px,#f7f7f7 100%)}
.topnav{position:absolute;left:12px;top:12px;width:1016px;height:48px;background:#fff;box-shadow:0 2px 6px rgba(0,0,0,.08);font-size:11px;font-weight:700}
.brand{position:absolute;left:46px;top:0;line-height:48px;font-size:15px;font-weight:700}
.range{position:absolute;top:0;height:48px;width:72px;line-height:48px;text-align:center;border-right:1px solid var(--line)}
.range.active{background:var(--navy);color:#fff}
.util{position:absolute;top:0;height:48px;display:flex;align-items:center;justify-content:center;gap:6px;border-left:1px solid var(--line);font-size:10.5px}
.tabs .tab{position:absolute;width:124px;background:#fff;font-size:10.5px;font-weight:600;color:#444;text-align:center;border-radius:3px 3px 0 0}
.tab.low{top:108px;height:28px;line-height:28px}
.tab.mid{top:100px;height:36px;line-height:36px}
.tab.active{top:92px;height:44px;line-height:44px;background:var(--ink);color:#fff;font-weight:700}
.badge{position:absolute;left:56px;width:260px;height:32px;border-radius:3px;color:#fff;font-size:13.5px;font-weight:600;text-align:center;line-height:32px}
.badge.sel{top:168px;background:var(--navy)}
.badge.unsel{top:476px;background:var(--grey-badge)}
table.factors{position:absolute;left:56px;width:928px;border-collapse:collapse;background:#fff;box-shadow:0 2px 6px rgba(0,0,0,.08)}
.factors th{height:56px;background:var(--teal);color:#fff;font-size:13.5px;font-weight:600;width:144px;border-left:1px solid rgba(255,255,255,.25)}
.factors th.id{background:var(--ink);width:352px;border:0}
.factors td{height:56px;text-align:center;font-family:'Roboto Condensed',sans-serif;font-size:15px;border-left:1px solid var(--line)}
.factors td:first-child{border:0}
.factors tr:nth-child(even) td{background:var(--row-alt)}
.chart-card{position:absolute;left:56px;top:784px;width:928px;height:340px;background:#fff;box-shadow:0 2px 8px rgba(0,0,0,.1)}
.chart-head{position:absolute;left:0;top:0;width:928px;height:68px;background:#efefef}
.ctab{position:absolute;width:72px;background:#fff;font-size:10.5px;font-weight:600;color:#555;text-align:center;border-radius:3px 3px 0 0}
.ctab.chart{left:44px;width:124px;top:40px;height:28px;line-height:28px;background:var(--navy);color:#fff}
.ctab.low{top:40px;height:28px;line-height:28px}
.ctab.mid{top:36px;height:32px;line-height:32px}
.ctab.active{top:32px;height:36px;line-height:36px;background:var(--ink);color:#fff}
svg.plot{position:absolute;left:0;top:0}
</style>
</head>
<body>
<div class="frame"></div>

<header class="topnav">
  <div class="brand">PELLCORE</div>
  <div class="range active" style="left:144px">250D</div>
  <div class="range" style="left:216px">83D</div>
  <div class="range" style="left:288px">42D</div>
  <div class="util" style="left:604px;width:113px">
    <svg width="18" height="18" viewBox="0 0 18 18"><path d="M2 9 9 2l7 7M4 7.5V16h4v-4h2v4h4V7.5" fill="none" stroke="#1b1b1b" stroke-width="1.8"/></svg>MODELS</div>
  <div class="util" style="left:717px;width:141px">
    <svg width="18" height="18" viewBox="0 0 18 18"><circle cx="9" cy="9" r="3" fill="none" stroke="#1b1b1b" stroke-width="1.5"/><circle cx="9" cy="9" r="6.5" fill="none" stroke="#1b1b1b" stroke-width="1.5" stroke-dasharray="2 2"/></svg>SENSITIVITIES</div>
  <div class="util" style="left:858px;width:146px">
    <svg width="18" height="18" viewBox="0 0 18 18"><path d="M9 1.5l2.3 4.8 5.2.7-3.8 3.6.9 5.2L9 13.3l-4.6 2.5.9-5.2L1.5 7l5.2-.7z" fill="none" stroke="#1b1b1b" stroke-width="1.4"/></svg>FAVOURITES</div>
</header>

<nav class="tabs">
  <div class="tab low" style="left:56px">EQUITIES</div>
  <div class="tab low" style="left:184px">ETFS</div>
  <div class="tab mid" style="left:312px">PAIRS</div>
  <div class="tab active" style="left:440px">ETF PAIRS</div>
  <div class="tab mid" style="left:568px">FACTORS</div>
  <div class="tab low" style="left:696px">NEW TAB TITLE #1</div>
  <div class="tab low" style="left:824px">NEW TAB TITLE #2</div>
  <div class="tab low" style="left:952px;width:32px"><svg width="12" height="14" viewBox="0 0 12 14" style="margin-top:7px"><path d="M3 1l6 6-6 6" fill="none" stroke="#777" stroke-width="2"/></svg></div>
  <div class="tab low" style="left:988px;width:32px;background:var(--navy)"><svg width="20" height="20" viewBox="0 0 20 20" style="margin-top:4px"><circle cx="10" cy="10" r="8" fill="none" stroke="#fff" stroke-width="1.6"/><path d="M10 6v8M6 10h8" stroke="#fff" stroke-width="1.6"/></svg></div>
</nav>

<div class="badge sel">Number of Selected Factors : 3</div>
<table class="factors" style="top:212px">
  <tr><th class="id">ID ⌄</th><th>Stat 1</th><th>Stat 2</th><th>Stat 3</th><th>Stat 4</th></tr>
  <tr><td>Factor 1</td><td>-1.4</td><td>0.094</td><td>6.1</td><td>100</td></tr>
  <tr><td>Factor 2</td><td>2.8</td><td>0.085</td><td>3.1</td><td>0.7</td></tr>
  <tr><td>Factor 3</td><td>-3.7</td><td>2.7</td><td>-7.2</td><td>100</td></tr>
</table>

<div class="badge unsel">Unselected Factors</div>
<table class="factors" style="top:520px">
  <tr><th class="id">ID ⌄</th><th>Stat 1</th><th>Stat 2</th><th>Stat 3</th><th>Stat 4</th></tr>
  <tr><td>Factor 4</td><td>-1.4</td><td>0.094</td><td>6.1</td><td>100</td></tr>
  <tr><td>Factor 5</td><td>2.8</td><td>0.085</td><td>3.1</td><td>0.7</td></tr>
  <tr><td>Factor 6</td><td>-3.7</td><td>2.7</td><td>-7.2</td><td>100</td></tr>
</table>

<section class="chart-card">
  <div class="chart-head"></div>
  <div class="ctab chart">CHART</div>
  <div class="ctab low" style="left:172px">#1</div>
  <div class="ctab low" style="left:248px">#2</div>
  <div class="ctab mid" style="left:324px">#3</div>
  <div class="ctab active" style="left:400px">#4</div>

  <svg class="plot" width="928" height="340" viewBox="56 784 928 340" font-family="Montserrat, sans-serif" font-size="9" fill="#555">
    <g stroke="#ececec" stroke-width="1">
      <line x1="120" y1="902" x2="860" y2="902"/><line x1="120" y1="932" x2="860" y2="932"/>
      <line x1="120" y1="962" x2="860" y2="962"/><line x1="120" y1="992" x2="860" y2="992"/>
      <line x1="120" y1="1022" x2="860" y2="1022"/>
      <line x1="146" y1="890" x2="146" y2="1052"/><line x1="260" y1="890" x2="260" y2="1052"/>
      <line x1="372" y1="890" x2="372" y2="1052"/><line x1="484" y1="890" x2="484" y2="1052"/>
      <line x1="594" y1="890" x2="594" y2="1052"/><line x1="706" y1="890" x2="706" y2="1052"/>
      <line x1="818" y1="890" x2="818" y2="1052"/>
    </g>
    <line x1="120" y1="1052" x2="860" y2="1052" stroke="#888"/>
    <g text-anchor="end"><text x="121" y="905">100</text><text x="121" y="935">80</text><text x="121" y="965">60</text><text x="121" y="995">40</text><text x="121" y="1025">20</text><text x="121" y="1055">0</text></g>
    <g text-anchor="middle"><text x="146" y="1072">Jul 2018</text><text x="260" y="1072">Sep 2018</text><text x="372" y="1072">Nov 2018</text><text x="484" y="1072">Jan 2019</text><text x="594" y="1072">Mar 2019</text><text x="706" y="1072">May 2019</text><text x="818" y="1072">Jul 2019</text></g>

    <!-- flat runs -->
    <line x1="162" y1="902" x2="228" y2="902" stroke="var(--olive)" stroke-width="5" stroke-linecap="round" stroke-dasharray="0 4.5"/>
    <line x1="600" y1="904" x2="800" y2="904" stroke="var(--olive)" stroke-width="5" stroke-linecap="round" stroke-dasharray="0 5"/>
    <line x1="472" y1="902" x2="822" y2="902" stroke="var(--blue)" stroke-width="5" stroke-linecap="round" stroke-dasharray="0 4.5"/>

    <g fill="var(--olive)">
      <circle cx="232" cy="906" r="2.8"/><circle cx="238" cy="914" r="2.8"/><circle cx="244" cy="903" r="2.8"/><circle cx="250" cy="908" r="2.8"/><circle cx="256" cy="904" r="2.8"/><circle cx="262" cy="910" r="2.8"/>
      <circle cx="268" cy="956" r="2.8"/><circle cx="272" cy="980" r="2.8"/><circle cx="276" cy="996" r="2.8"/><circle cx="280" cy="966" r="2.8"/><circle cx="285" cy="986" r="2.8"/><circle cx="290" cy="1000" r="2.8"/><circle cx="295" cy="978" r="2.8"/><circle cx="300" cy="990" r="2.8"/>
      <circle cx="306" cy="950" r="2.8"/><circle cx="310" cy="928" r="2.8"/><circle cx="316" cy="916" r="2.8"/><circle cx="320" cy="904" r="2.8"/><circle cx="326" cy="906" r="2.8"/>
      <circle cx="330" cy="950" r="2.8"/><circle cx="334" cy="966" r="2.8"/><circle cx="340" cy="976" r="2.8"/><circle cx="344" cy="970" r="2.8"/>
      <circle cx="350" cy="1026" r="2.8"/><circle cx="356" cy="1036" r="2.8"/><circle cx="362" cy="1040" r="2.8"/><circle cx="368" cy="1046" r="2.8"/><circle cx="374" cy="1044" r="2.8"/><circle cx="380" cy="1040" r="2.8"/><circle cx="386" cy="1034" r="2.8"/><circle cx="392" cy="1026" r="2.8"/><circle cx="398" cy="1016" r="2.8"/><circle cx="404" cy="1006" r="2.8"/><circle cx="410" cy="996" r="2.8"/><circle cx="416" cy="988" r="2.8"/><circle cx="422" cy="974" r="2.8"/><circle cx="428" cy="958" r="2.8"/>
      <circle cx="434" cy="904" r="2.8"/><circle cx="440" cy="908" r="2.8"/><circle cx="446" cy="904" r="2.8"/><circle cx="452" cy="910" r="2.8"/><circle cx="458" cy="918" r="2.8"/>
      <circle cx="462" cy="1044" r="2.8"/><circle cx="468" cy="1048" r="2.8"/><circle cx="474" cy="1042" r="2.8"/><circle cx="480" cy="1040" r="2.8"/><circle cx="486" cy="1034" r="2.8"/><circle cx="492" cy="1030" r="2.8"/><circle cx="498" cy="1036" r="2.8"/><circle cx="504" cy="1044" r="2.8"/><circle cx="508" cy="1034" r="2.8"/>
      <circle cx="514" cy="1014" r="2.8"/><circle cx="518" cy="1000" r="2.8"/><circle cx="524" cy="978" r="2.8"/><circle cx="528" cy="960" r="2.8"/><circle cx="534" cy="950" r="2.8"/>
      <circle cx="538" cy="920" r="2.8"/><circle cx="544" cy="930" r="2.8"/><circle cx="550" cy="918" r="2.8"/><circle cx="554" cy="1022" r="2.8"/><circle cx="560" cy="1030" r="2.8"/><circle cx="566" cy="938" r="2.8"/><circle cx="570" cy="920" r="2.8"/><circle cx="574" cy="930" r="2.8"/><circle cx="578" cy="994" r="2.8"/><circle cx="582" cy="912" r="2.8"/><circle cx="590" cy="918" r="2.8"/><circle cx="596" cy="910" r="2.8"/>
    </g>
    <g fill="var(--blue)">
      <circle cx="162" cy="960" r="2.8"/><circle cx="166" cy="910" r="2.8"/><circle cx="172" cy="906" r="2.8"/>
      <circle cx="178" cy="970" r="2.8"/><circle cx="182" cy="994" r="2.8"/><circle cx="186" cy="1006" r="2.8"/><circle cx="190" cy="1014" r="2.8"/><circle cx="196" cy="1000" r="2.8"/><circle cx="200" cy="1018" r="2.8"/><circle cx="205" cy="966" r="2.8"/><circle cx="210" cy="984" r="2.8"/><circle cx="216" cy="968" r="2.8"/><circle cx="222" cy="1016" r="2.8"/><circle cx="228" cy="988" r="2.8"/><circle cx="234" cy="1004" r="2.8"/><circle cx="240" cy="1012" r="2.8"/><circle cx="246" cy="1018" r="2.8"/><circle cx="252" cy="1010" r="2.8"/>
      <circle cx="260" cy="1034" r="2.8"/><circle cx="266" cy="1036" r="2.8"/><circle cx="272" cy="1032" r="2.8"/><circle cx="280" cy="1028" r="2.8"/><circle cx="286" cy="1036" r="2.8"/><circle cx="292" cy="1032" r="2.8"/>
      <circle cx="300" cy="1018" r="2.8"/><circle cx="306" cy="1008" r="2.8"/><circle cx="312" cy="1016" r="2.8"/><circle cx="318" cy="1010" r="2.8"/><circle cx="324" cy="1024" r="2.8"/><circle cx="330" cy="1012" r="2.8"/><circle cx="336" cy="1016" r="2.8"/><circle cx="342" cy="1020" r="2.8"/>
      <circle cx="346" cy="1048" r="2.8"/><circle cx="354" cy="1042" r="2.8"/><circle cx="360" cy="1022" r="2.8"/><circle cx="366" cy="1028" r="2.8"/>
      <circle cx="370" cy="948" r="2.8"/><circle cx="374" cy="918" r="2.8"/><circle cx="380" cy="914" r="2.8"/><circle cx="384" cy="904" r="2.8"/><circle cx="388" cy="926" r="2.8"/><circle cx="394" cy="922" r="2.8"/>
      <circle cx="398" cy="1036" r="2.8"/><circle cx="404" cy="1028" r="2.8"/><circle cx="410" cy="1016" r="2.8"/><circle cx="416" cy="1026" r="2.8"/><circle cx="422" cy="1006" r="2.8"/><circle cx="428" cy="988" r="2.8"/><circle cx="434" cy="1006" r="2.8"/><circle cx="438" cy="984" r="2.8"/>
      <circle cx="436" cy="918" r="2.8"/><circle cx="442" cy="912" r="2.8"/><circle cx="448" cy="904" r="2.8"/><circle cx="454" cy="912" r="2.8"/><circle cx="460" cy="906" r="2.8"/><circle cx="466" cy="902" r="2.8"/>
    </g>
    <circle cx="800" cy="1050" r="2.8" fill="var(--green)"/><circle cx="805" cy="1050" r="2.8" fill="var(--green)"/>

    <g>
      <text x="906" y="904" font-family="serif" font-size="9.5" fill="#444">Names</text>
      <circle cx="892" cy="901" r="2.6" fill="#8ab4d8"/><circle cx="892" cy="916" r="2.6" fill="#f0b27a"/>
      <circle cx="892" cy="931" r="2.6" fill="var(--green)"/><circle cx="892" cy="946" r="2.6" fill="#e07b7b"/>
      <circle cx="892" cy="961" r="2.6" fill="#c3a6d6"/><circle cx="892" cy="976" r="2.6" fill="#b49a8f"/>
      <circle cx="892" cy="991" r="2.6" fill="#e8aed0"/><circle cx="892" cy="1006" r="2.6" fill="#bcbcbc"/>
      <circle cx="892" cy="1021" r="2.6" fill="var(--olive)"/><circle cx="892" cy="1036" r="2.6" fill="#8fd3dc"/>
      <circle cx="892" cy="1051" r="2.6" fill="var(--blue)"/>
    </g>
  </svg>
</section>
</body>
</html>
```